Norvane Stationery Design Project

We need stationary design that goes with the attached logo. We have logo in two different versions. One in Red/Black and the other in Blue/Green. Red/Black is going to be our primary color and we are planning to use Blue/Green occasionally as necessary.

So we need stationary design in both color combinations. Maybe you can work with Red/Black first and once we decide on the design, then you can show the Blue/Green variation.

Please see the attached png and psd files for logo.

Target Market(s)

IT departments of Medium size Enterprises.

Industry/Entity Type

Work

Requirements
Must have
• -Letter head
-Cover page design for white papers and articles that are going to publish
-Business Card
-Envelope design
Nice to have
• - High level design template that we can follow for our internal web applications

```html
<!DOCTYPE html>
<html lang="en">
<head>
<meta charset="utf-8">
<title>Norvane Software – Business Card</title>
<link href="https://fonts.googleapis.com/css2?family=Lato:wght@400;700;900&family=Cinzel:wght@400&display=swap" rel="stylesheet">
<style>
  :root {
    --stage: #2b2b2b;
    --paper: #ffffff;
    --paper-shade: #ececec;
    --red: #d3161c;
    --red-deep: #9e0c10;
    --ink: #161616;
    --on-red: #f3d6d6;
    --on-red-soft: #f0b9b9;
  }
  * { box-sizing: border-box; margin: 0; padding: 0; }
  html, body { width: 1200px; height: 997px; overflow: hidden; }
  body {
    background: var(--stage);
    font-family: "Lato", Arial, sans-serif;
    display: flex;
    align-items: center;
    justify-content: center;
    gap: 40px;
  }
  .card {
    position: relative;
    width: 540px;
    height: 310px;
    border-radius: 18px;
    overflow: hidden;
    background: linear-gradient(180deg, var(--paper) 0%, var(--paper-shade) 100%);
  }
  .card__band {
    position: absolute;
    left: 0; right: 0; bottom: 0;
    height: 42%;
    background: linear-gradient(180deg, var(--red) 0%, var(--red-deep) 100%);
  }
  .card__rules {
    position: absolute;
    left: 0; right: 0;
    bottom: 42%;
    height: 14px;
    background:
      linear-gradient(var(--red), var(--red)) 0 0 / 100% 2px no-repeat,
      linear-gradient(var(--red), var(--red)) 0 5px / 100% 2px no-repeat,
      linear-gradient(var(--red), var(--red)) 0 10px / 100% 2px no-repeat;
  }
  .brand {
    position: absolute;
    display: flex;
    align-items: center;
    gap: 16px;
    color: var(--ink);
    font-weight: 900;
    letter-spacing: 0.12em;
    text-transform: uppercase;
  }
  .brand__mark {
    width: 52px; height: 52px;
    background: var(--red);
    flex: none;
  }
  .brand__name { font-size: 30px; line-height: 1.1; }
  .brand__name span { display: block; font-size: 17px; letter-spacing: 0.42em; }
  .card--front .brand { left: 120px; top: 58px; }
  .card--back .brand { left: 120px; top: 42px; }

  .tagline {
    position: absolute;
    left: 0; right: 0; bottom: 52px;
    text-align: center;
    color: var(--on-red-soft);
    font-size: 14px;
    letter-spacing: 0.25em;
    text-transform: uppercase;
  }
  .holder {
    position: absolute;
    left: 34px; bottom: 36px;
    color: var(--on-red);
  }
  .holder__name {
    font-family: "Cinzel", Georgia, serif;
    font-size: 26px;
    letter-spacing: 0.03em;
  }
  .holder__role {
    font-size: 15px;
    font-weight: 700;
    letter-spacing: 0.02em;
  }
  .contact {
    position: absolute;
    right: 30px; bottom: 26px;
    list-style: none;
    color: var(--on-red);
    font-size: 14px;
  }
  .contact li {
    display: flex;
    align-items: center;
    gap: 8px;
    height: 26px;
  }
  .contact svg { width: 18px; height: 18px; flex: none; }
  .contact__web { font-weight: 900; font-size: 15px; margin-top: 2px; }
</style>
</head>
<body>

  <article class="card card--front" aria-label="Business card, front">
    <div class="brand">
      <div class="brand__mark"></div>
      <div class="brand__name">Norvane<span>Software</span></div>
    </div>
    <div class="card__rules"></div>
    <div class="card__band"></div>
    <p class="tagline">Your slogan / tagline here</p>
  </article>

  <article class="card card--back" aria-label="Business card, back">
    <div class="brand">
      <div class="brand__mark"></div>
      <div class="brand__name">Norvane<span>Software</span></div>
    </div>
    <div class="card__rules"></div>
    <div class="card__band"></div>

    <div class="holder">
      <p class="holder__name">DANA WHITLOCK</p>
      <p class="holder__role">FOUNDER/CEO</p>
    </div>

    <ul class="contact">
      <li>
        <svg viewBox="0 0 18 18" aria-hidden="true"><rect width="18" height="18" rx="2" fill="#f3d6d6"/><path d="M4 6c0-1 1-2 2-2h6c1 0 2 1 2 2l-2 1-1-1H7L6 7z M5 9h8l1 5H4z" fill="#b31015"/></svg>
        <span>555 014 7950</span>
      </li>
      <li>
        <svg viewBox="0 0 18 18" aria-hidden="true"><rect width="18" height="18" rx="2" fill="#f3d6d6"/><path d="M6 3h6v4H6z M3 8h12v6h-3v2H6v-2H3z" fill="#b31015"/><rect x="7" y="12" width="4" height="3" fill="#f3d6d6"/></svg>
        <span>555 014 7000</span>
      </li>
      <li>
        <svg viewBox="0 0 18 18" aria-hidden="true"><rect width="18" height="18" rx="2" fill="#f3d6d6"/><rect x="3" y="5" width="12" height="8" fill="none" stroke="#b31015" stroke-width="1.4"/><path d="M3 5l6 5 6-5" fill="none" stroke="#b31015" stroke-width="1.4"/></svg>
        <span>dana@norvanesoftware.com</span>
      </li>
      <li class="contact__web">www.norvanesoftware.com</li>
    </ul>
  </article>

</body>
</html>
```